IT Company requires new Business Card design.

Over the years we have had a few different business card designs. We are now due for new cards across the board for all staff. We felt this would be a good time to start fresh with a new design. Our traditional card simply had our details on the front, and a list of services on the back. We don't particularly need the list of services, we have had cards where the only thing on the rear of the card was our logo.
Feel free to be creative, we would like our tag line "Complete IT Management" to appear at some point, doesn't necessarily have to be with the logo.
I have attached samples and drafts of various previous cards we have used over the years.

```html
<!DOCTYPE html>
<html lang="en">
<head>
<meta charset="utf-8">
<title>Ridgeway Networking – Business Card</title>
<link rel="stylesheet" href="https://fonts.googleapis.com/css2?family=Open+Sans:wght@300;600&display=swap">
<style>
  :root {
    --card-centre: #6a7a8b;
    --card-mid: #5d6f82;
    --card-edge: #465c75;
    --text-main: #ffffff;
    --text-soft: #eef2f6;
    --divider: rgba(255, 255, 255, 0.85);
  }
  * { box-sizing: border-box; margin: 0; padding: 0; }
  html, body {
    width: 1200px;
    height: 670px;
    overflow: hidden;
    background: var(--card-edge);
  }
  .card {
    position: relative;
    width: 1200px;
    height: 670px;
    overflow: hidden;
    font-family: "Open Sans", "Segoe UI", sans-serif;
    color: var(--text-main);
    background:
      radial-gradient(ellipse 62% 78% at 50% 42%, var(--card-centre) 0%, var(--card-mid) 55%, var(--card-edge) 100%);
  }
  .tagline {
    position: absolute;
    left: 54px;
    top: 140px;
    font-size: 34px;
    font-weight: 600;
    letter-spacing: 0.4px;
  }
  .web-address {
    position: absolute;
    left: 55px;
    top: 190px;
    font-size: 23px;
    font-weight: 300;
    color: var(--text-soft);
  }
  .brand-name {
    position: absolute;
    right: 66px;
    top: 112px;
    width: 240px;
    text-align: right;
    font-size: 34px;
    font-weight: 600;
    line-height: 1.15;
    color: var(--text-main);
  }
  .services {
    position: absolute;
    top: 404px;
    font-size: 26px;
    font-weight: 300;
    line-height: 38px;
    list-style: none;
    color: var(--text-soft);
    white-space: nowrap;
  }
  .services--hardware { left: 40px; }
  .services--infrastructure { left: 365px; }
  .services--online { left: 804px; top: 402px; }
  .divider {
    position: absolute;
    top: 391px;
    width: 1px;
    height: 212px;
    background: var(--divider);
  }
  .divider--first { left: 283px; }
  .divider--second { left: 723px; }
</style>
</head>
<body>
  <main class="card">
    <h1 class="tagline">Complete IT Management</h1>
    <p class="web-address">www.ridgewaynetworking.com.au</p>

    <p class="brand-name">Ridgeway Networking</p>

    <ul class="services services--hardware">
      <li>Networking</li>
      <li>Servers</li>
      <li>Workstations</li>
      <li>Laptops</li>
      <li>Firewalls</li>
    </ul>
    <span class="divider divider--first"></span>
    <ul class="services services--infrastructure">
      <li>Data Cabling</li>
      <li>All electrical Work</li>
      <li>Server Racks</li>
      <li>Network Infrastructure</li>
      <li>Off site back up</li>
    </ul>
    <span class="divider divider--second"></span>
    <ul class="services services--online">
      <li>ADSL Connections</li>
      <li>Web Hosting</li>
      <li>Web Design</li>
      <li>Website Maintenance</li>
      <li>Domain Names PABX systems</li>
    </ul>
  </main>
</body>
</html>
```